Corvane Freight Company Business Card Design

We are a company that delivers natural saltwater (from the ocean) to aquarium companies, restaurants and home marine tanks. I would like a new business card to suit.

Must include Name, company name, abn, contact number and website as well as logo (see attached).

Looking for a design that stands out, has a clean but unique appearance.

Double and single sided entries welcome

Business

• Logo

```html
<!DOCTYPE html>
<html lang="en">
<head>
<meta charset="utf-8">
<title>Corvane Freight Company – Business Card</title>
<link href="https://fonts.googleapis.com/css2?family=Open+Sans:wght@400;600;700&display=swap" rel="stylesheet">
<style>
  :root {
    --stage: #26272a;
    --front-blue: #1f6ee6;
    --wave-blue: #3fa9f5;
    --wave-light: #8fe2f7;
    --back-cyan: #7fe3f4;
    --back-glow: #c9f6fb;
    --white: #ffffff;
    --ink-blue: #2f9be8;
  }
  html, body {
    margin: 0;
    padding: 0;
    width: 1200px;
    height: 1006px;
    overflow: hidden;
    background: var(--stage);
    font-family: "Open Sans", sans-serif;
  }
  .canvas { position: relative; width: 1200px; height: 1006px; }
  .card {
    position: absolute;
    border-radius: 20px;
    overflow: hidden;
  }
  .card-front {
    left: 87px; top: 83px; width: 707px; height: 401px;
    background: var(--front-blue);
    color: var(--white);
  }
  .card-front .waves { position: absolute; inset: 0; }
  .holder {
    position: absolute; right: 42px; top: 22px; text-align: right;
  }
  .holder-name { margin: 0; font-size: 30px; font-weight: 700; line-height: 1.2; }
  .holder-title { margin: 2px 0 0; font-size: 21px; font-weight: 400; }
  .brand-name {
    position: absolute; left: 40px; top: 160px;
    margin: 0; font-size: 52px; font-weight: 700; line-height: 1;
    color: var(--white); letter-spacing: -0.5px;
  }
  .contact {
    position: absolute; left: 40px; top: 292px;
    font-size: 16.5px; line-height: 27px;
  }
  .contact p { margin: 0; display: flex; align-items: center; gap: 6px; }
  .contact svg { width: 14px; height: 14px; }
  .divider {
    position: absolute; left: 236px; top: 320px;
    width: 2px; height: 46px; background: var(--wave-light);
  }
  .company {
    position: absolute; left: 256px; top: 320px;
    font-size: 16.5px; line-height: 24px;
  }
  .company p { margin: 0; }
  .company .legal { font-weight: 700; }
  .card-back {
    left: 404px; top: 533px; width: 706px; height: 402px;
    background: radial-gradient(ellipse at 50% 65%, var(--back-glow) 0%, var(--back-cyan) 70%);
    text-align: center;
  }
  .back-brand {
    position: absolute; left: 0; right: 0; top: 148px;
    margin: 0; font-size: 56px; font-weight: 700; line-height: 1;
    color: var(--ink-blue); letter-spacing: -0.5px;
  }
  .back-web {
    position: absolute; left: 0; right: 0; top: 318px;
    margin: 0; font-size: 21px; letter-spacing: 5px; color: var(--white);
  }
</style>
</head>
<body>
<main class="canvas">
  <section class="card card-front" aria-label="Front of business card">
    <svg class="waves" viewBox="0 0 707 401" preserveAspectRatio="none" aria-hidden="true">
      <path d="M0 0 H707 V250 C560 120 320 60 0 92 Z" fill="var(--wave-blue)"/>
      <path d="M0 92 C320 60 560 120 707 250 V262 C560 140 320 82 0 108 Z" fill="var(--wave-light)"/>
    </svg>
    <div class="holder">
      <p class="holder-name">Your name</p>
      <p class="holder-title">Title</p>
    </div>
    <p class="brand-name">Corvane Freight</p>
    <div class="contact">
      <p><svg viewBox="0 0 16 16" aria-hidden="true"><circle cx="8" cy="8" r="7" fill="none" stroke="currentColor" stroke-width="1.4"/><path d="M5 4.5 L6.6 4.5 L7.2 6.4 L6.3 7.1 C6.8 8.2 7.8 9.2 8.9 9.7 L9.6 8.8 L11.5 9.4 L11.5 11 C8 11.3 4.7 8 5 4.5 Z" fill="currentColor"/></svg>123-456-7890</p>
      <p><svg viewBox="0 0 16 16" aria-hidden="true"><circle cx="8" cy="8" r="7" fill="currentColor"/><path d="M1 8 H15 M8 1 C5 4 5 12 8 15 M8 1 C11 4 11 12 8 15" stroke="var(--front-blue)" stroke-width="1" fill="none"/></svg>www.website.com</p>
      <p>ABN : 0123456789</p>
    </div>
    <div class="divider"></div>
    <div class="company">
      <p class="legal">Corvane Freight LLC</p>
      <p>Street Name, City Name, State, City Zip Code</p>
    </div>
  </section>

  <section class="card card-back" aria-label="Back of business card">
    <p class="back-brand">Corvane Freight</p>
    <p class="back-web">www.website.com</p>
  </section>
</main>
</body>
</html>
```